Business Cards Design for the electrical wholesaler: clean bold dynamic :)

We need a business card design that would follow our latest brand guidelines. As an electrical wholesaler we want to bring a fresh look and feel into the industry. The design should be clean bold and dynamic. It should come alive with the renewed energy of our green colour. Our grey colour should keep things balanced and complement the notion of maturity and responsibility. We employ Lato as a corporate font however are not bound by this font and we’re open to interpretation here.

Target Market(s)

Electrical contractors

Industry/Entity Type

Business

Contact Information for Business Card

Logo
Name & Surname: Halyna Dorosh
Job Title: Director of Marketing
Email: halya.dorosh@quillmail.example
Cell phone: XXX.XXX.XXXX
Address: 20517 - 87 Ave. Edmonton, AB, Canada. T6K 4N8
Business Phone: 780.555.0184
Website: www.brovix.example

Font styles to use
Other font styles liked:
• Lato

Requirements
Must have
• Logo & website
Nice to have
• Brand elements - some of them you may find in the attached Brand Guidelines (e.g. three lines on the background signifying "W")

```html
<!DOCTYPE html>
<html lang="en">
<head>
<meta charset="utf-8">
<title>Brovix business card</title>
<link rel="stylesheet" href="https://fonts.googleapis.com/css2?family=Work+Sans:wght@400;500;600&display=swap">
<style>
  :root {
    --green: #8cc63f;
    --grey: #505052;
    --ink: #3d3d3f;
    --paper: #ffffff;
    --stage: #1b1b1b;
    --back-dark: #1c1c1c;
    --back-light: #363534;
  }
  * { margin: 0; padding: 0; box-sizing: border-box; }
  html, body { width: 1200px; height: 897px; overflow: hidden; background: var(--stage); }
  body { position: relative; font-family: "Work Sans", sans-serif; }

  .card {
    position: absolute;
    left: 303px;
    width: 595px;
    height: 338px;
    border-radius: 22px;
    overflow: hidden;
  }
  .card--front { top: 92px; background: var(--paper); }
  .card--back {
    top: 469px;
    background: radial-gradient(ellipse at 80% 85%, var(--back-light) 0%, var(--back-dark) 65%);
  }

  .brand {
    position: absolute;
    display: flex;
    align-items: center;
    gap: 10px;
    font-weight: 600;
    letter-spacing: -0.5px;
    line-height: 1;
  }
  .brand__dot { background: var(--green); border-radius: 50%; flex: none; }

  .brand--front { left: 33px; top: 34px; font-size: 44px; color: var(--grey); }
  .brand--front .brand__dot { width: 22px; height: 22px; }

  .brand--large {
    right: 36px; top: 196px;
    font-size: 92px; color: var(--grey);
    letter-spacing: -2px;
  }

  .brand--back {
    left: 50%; top: 50%;
    transform: translate(-50%, -50%);
    font-size: 70px; color: #ffffff; gap: 16px;
  }
  .brand--back .brand__dot { width: 34px; height: 34px; }

  .person { position: absolute; right: 34px; top: 34px; text-align: right; }
  .person__name { font-size: 24px; font-weight: 500; color: var(--green); line-height: 1.1; }
  .person__title { font-size: 15px; color: var(--ink); letter-spacing: 0.6px; margin-top: 4px; }

  .contact { position: absolute; left: 33px; top: 210px; list-style: none; }
  .contact__item {
    display: flex; align-items: center; gap: 10px;
    font-size: 14.5px; color: var(--ink); letter-spacing: 0.5px; height: 19px;
  }
  .contact__icon { width: 11px; height: 11px; flex: none; }
  .contact__accent { color: var(--green); }

  .address {
    position: absolute; left: 33px; top: 275px;
    font-size: 14.5px; color: var(--ink); letter-spacing: 0.5px; line-height: 20px;
    font-style: normal;
  }
</style>
</head>
<body>

  <section class="card card--front" aria-label="Card front">
    <div class="brand brand--front"><span class="brand__dot"></span>brovix</div>

    <div class="person">
      <p class="person__name">Halyna Dorosh</p>
      <p class="person__title">Founder</p>
    </div>

    <ul class="contact">
      <li class="contact__item">
        <svg class="contact__icon" viewBox="0 0 12 12"><path d="M2.5 1 L4.5 1 L5 3.5 L3.8 4.4 C4.4 6 5.8 7.5 7.6 8.2 L8.5 7 L11 7.5 L11 9.5 C11 10.4 10.3 11 9.4 11 C5 10.6 1.4 7 1 2.6 C1 1.7 1.6 1 2.5 1 Z" fill="var(--green)"/></svg>
        780.555.0184
      </li>
      <li class="contact__item">
        <svg class="contact__icon" viewBox="0 0 12 12"><rect x="1" y="2.5" width="10" height="7" fill="none" stroke="var(--green)" stroke-width="1.3"/><path d="M1 2.8 L6 6.5 L11 2.8" fill="none" stroke="var(--green)" stroke-width="1.3"/></svg>
        hello@brovix.example
      </li>
      <li class="contact__item">
        <svg class="contact__icon" viewBox="0 0 12 12"><circle cx="6" cy="6" r="5" fill="none" stroke="var(--green)" stroke-width="1.1"/><ellipse cx="6" cy="6" rx="2.2" ry="5" fill="none" stroke="var(--green)" stroke-width="1"/><path d="M1 6 H11 M2 3.5 H10 M2 8.5 H10" stroke="var(--green)" stroke-width="0.9"/></svg>
        <span>www.<span class="contact__accent">brovix</span>.example</span>
      </li>
    </ul>

    <address class="address">
      20517 87ave<br>
      T6K4N8 Edmonton, Alberta
    </address>

    <div class="brand brand--large">brovix</div>
  </section>

  <section class="card card--back" aria-label="Card back">
    <div class="brand brand--back"><span class="brand__dot"></span>brovix</div>
  </section>

</body>
</html>
```